Brookvale Building Company - advertisement poster

I am looking to print some canvas signs to advertise my general contracting company, Brookvale Building Company. The sign will measure 6' long x 3' high so the size should match that ratio. I already have a logo icon, which is the Letter 'B' and some trees that I would like to incorporate, see attached. I would also like the to have the following information listed:
1) phone number: 831-555-0172
2) email: brookvalebuildingcompany@mailnest.example
3) website: brookvalebuildingcompany.example
4) Lic#4826130
5) I want to use this text: "BUILD WITH THE B-CREW!"

The ad should be relatively simple and clean. Black and Green are my company colors. I am open to creative ideas!

Target Market(s)

People looking to renovate their homes

Industry/Entity Type

Construction

Colors
59FF00
82FF00
B8FF75
E3FFCB
F4FFEA

Requirements
Must have
• Must have my company logo
Should not have
• No photos or complex graphics

```html
<!DOCTYPE html>
<html lang="en">
<head>
<meta charset="utf-8">
<title>Brookvale Building Company – Sign</title>
<link href="https://fonts.googleapis.com/css2?family=Archivo+Black&family=Michroma&family=Arimo:wght@700&display=swap" rel="stylesheet">
<style>
  :root {
    --page-bg: #ebebeb;
    --sign-black: #000000;
    --brand-green: #72b03c;
    --tree-light: rgba(122, 171, 60, 0.85);
    --tree-mid: rgba(96, 140, 52, 0.6);
    --white: #ffffff;
    --ink: #111111;
  }
  html, body {
    margin: 0;
    width: 1200px;
    height: 1200px;
    overflow: hidden;
    background: radial-gradient(circle at 50% 50%, #f7f7f7 0%, var(--page-bg) 70%);
  }
  .sign {
    position: absolute;
    left: 83px;
    top: 342px;
    width: 1034px;
    height: 516px;
    background: var(--sign-black);
    overflow: hidden;
  }
  .license {
    position: absolute;
    right: 27px;
    top: 18px;
    font: 700 21px "Arimo", sans-serif;
    letter-spacing: 3px;
    color: var(--white);
  }
  .headline-band {
    position: absolute;
    left: 0;
    top: 39px;
    width: 709px;
    height: 77px;
    background: var(--brand-green);
  }
  .headline {
    position: absolute;
    left: 33px;
    top: 50%;
    transform: translateY(-50%);
    margin: 0;
    font: 400 45px "Archivo Black", sans-serif;
    color: var(--white);
    text-shadow: 3px 3px 0 var(--ink);
    white-space: nowrap;
  }
  .est {
    position: absolute;
    top: 230px;
    width: 72px;
    text-align: center;
    font: 400 15px "Michroma", sans-serif;
    letter-spacing: 4px;
    color: var(--white);
    border-top: 1px solid var(--brand-green);
    border-bottom: 1px solid var(--brand-green);
    padding: 8px 0;
  }
  .est-left { left: 291px; }
  .est-right { left: 669px; }
  .brand-mark {
    position: absolute;
    left: 458px;
    top: 160px;
    width: 110px;
    height: 110px;
    background: var(--brand-green);
  }
  .brand-name {
    position: absolute;
    left: 0;
    right: 0;
    top: 300px;
    margin: 0;
    text-align: center;
    font: 400 52px/1 "Michroma", sans-serif;
    color: var(--white);
    white-space: nowrap;
  }
  .brand-name .sub {
    display: block;
    margin-top: 12px;
    font-size: 21px;
    letter-spacing: 11px;
    padding-left: 11px;
  }
  .website {
    position: absolute;
    left: 0;
    right: 0;
    top: 408px;
    text-align: center;
    font: 700 18px "Arimo", sans-serif;
    letter-spacing: 4px;
    color: var(--white);
  }
  .trees {
    position: absolute;
    top: 240px;
    width: 202px;
    height: 215px;
    background: radial-gradient(ellipse 50% 60% at 50% 55%, var(--tree-light) 0%, var(--tree-mid) 55%, rgba(0, 0, 0, 0) 100%);
  }
  .trees-left { left: 9px; }
  .trees-right { left: 818px; }
  .contact-band {
    position: absolute;
    left: 0;
    bottom: 0;
    width: 100%;
    height: 68px;
    background: var(--brand-green);
  }
  .phone {
    position: absolute;
    left: 30px;
    top: 50%;
    transform: translateY(-50%);
    font: 400 44px "Archivo Black", sans-serif;
    color: var(--white);
    text-shadow: 3px 3px 0 var(--ink);
  }
  .email {
    position: absolute;
    right: 27px;
    top: 50%;
    transform: translateY(-50%);
    font: 700 20px "Arimo", sans-serif;
    letter-spacing: 1.6px;
    color: var(--ink);
    white-space: nowrap;
  }
</style>
</head>
<body>
  <main class="sign">
    <div class="license">Lic#4826130</div>

    <div class="headline-band">
      <h1 class="headline">BUILD WITH THE B-CREW!</h1>
    </div>

    <div class="est est-left">ESTD</div>
    <div class="brand-mark"></div>
    <div class="est est-right">2020</div>

    <h2 class="brand-name">BROOKVALE<span class="sub">BUILDING COMPANY</span></h2>
    <div class="website">brookvalebuildingcompany.example</div>

    <div class="trees trees-left" role="img" aria-label="Illustration of two green pine trees"></div>
    <div class="trees trees-right" role="img" aria-label="Illustration of two green pine trees"></div>

    <footer class="contact-band">
      <div class="phone">831-555-0172</div>
      <div class="email">brookvalebuildingcompany@mailnest.example</div>
    </footer>
  </main>
</body>
</html>
```